Business Card Design for Marketing Firm

Looking for business card design for higher end marketing firm. Clean but impressionable/trendy. We are a marketing firm that represents manufacturers in the foodservice equipment and supply industry. Our customers are end users such has hotels, restaurants, country clubs, convention centers and casinos as well as distributors of restaurants supplies and equipment, and manufacturers of foodservice equipment and supplies.
Target Market(s)
Hotels, Restaurants, Supply & Equipment Distributors, Foodservice Manufacturers
Industry/Entity Type
Foodservice/Hospitality
Contact Information for Business Card
Name, Title, Contact Number, Email, Website, Social Media, Address
Requirements
Must have
- Clean & Simple but Serious and Impressionable

```html
<!DOCTYPE html>
<html lang="en">
<head>
<meta charset="utf-8">
<title>Larkmoor Trade Partners – Business Card</title>
<link href="https://fonts.googleapis.com/css2?family=Open+Sans:wght@400;600;700&display=swap" rel="stylesheet">
<style>
  :root {
    --navy: #282a74;
    --white: #ffffff;
    --backdrop: #d9d9d6;
    --ink: #1f1f2e;
  }
  * { margin: 0; padding: 0; box-sizing: border-box; }
  html, body {
    width: 1200px; height: 801px; overflow: hidden;
    background: var(--backdrop);
    font-family: "Open Sans", Arial, sans-serif;
  }
  .stage {
    width: 1200px; height: 801px;
    display: flex; align-items: center; justify-content: center; gap: 50px;
  }
  .card {
    position: relative;
    width: 540px; height: 310px;
    background: var(--white);
    border-radius: 18px;
    overflow: hidden;
    box-shadow: 0 6px 18px rgba(0,0,0,0.18);
  }
  .card-art { position: absolute; inset: 0; }

  /* Contact side */
  .name-block {
    position: absolute; top: 22px; right: 40px; text-align: right;
  }
  .name-block .name {
    font-weight: 700; font-size: 21px; letter-spacing: 0.5px;
    color: var(--navy); text-transform: uppercase; line-height: 1.1;
  }
  .name-block .title {
    font-size: 13px; color: var(--ink); margin-top: 2px;
  }
  .name-tab {
    position: absolute; top: 22px; right: 0; width: 22px; height: 24px;
    background: var(--navy);
  }
  .front-brand {
    position: absolute; left: 34px; top: 118px;
    display: flex; align-items: center; gap: 10px;
    font-weight: 600; font-size: 17px; color: var(--navy);
    text-transform: uppercase; letter-spacing: 1px; line-height: 1.25;
  }
  .brand-dot {
    width: 18px; height: 18px; border-radius: 50%; background: var(--navy);
    flex: none;
  }
  .contact {
    position: absolute; right: 26px; top: 112px;
    color: var(--white); font-size: 12.5px; line-height: 1.55; text-align: right;
  }
  .contact .address { margin-bottom: 12px; }
  .contact-line { display: flex; align-items: center; justify-content: flex-end; gap: 7px; }
  .contact-line svg { width: 12px; height: 12px; flex: none; }

  /* Brand side */
  .back-brand {
    position: absolute; left: 0; right: 0; top: 105px;
    display: flex; align-items: center; justify-content: center; gap: 14px;
    font-weight: 600; font-size: 30px; color: var(--navy);
    text-transform: uppercase; letter-spacing: 1.5px;
  }
  .back-brand .brand-dot { width: 26px; height: 26px; }
  .social-row {
    position: absolute; left: 0; right: 0; top: 212px;
    display: flex; justify-content: center; gap: 6px;
  }
  .social-dot {
    width: 18px; height: 18px; border-radius: 50%; background: var(--navy);
  }
  .back-edge {
    position: absolute; left: 0; right: 0; bottom: 0; height: 3px; background: var(--navy);
  }
</style>
</head>
<body>
<main class="stage">

  <section class="card card-front" aria-label="Business card, contact side">
    <svg class="card-art" viewBox="0 0 540 310" preserveAspectRatio="none" aria-hidden="true">
      <path d="M170 310 C 190 190, 330 90, 540 60 L540 310 Z" fill="var(--navy)"/>
      <path d="M188 310 C 206 198, 340 100, 540 70" fill="none" stroke="var(--white)" stroke-width="4"/>
      <path d="M228 310 C 236 250, 262 190, 296 159" fill="none" stroke="var(--white)" stroke-width="3"/>
    </svg>
    <div class="name-tab"></div>
    <div class="name-block">
      <div class="name">Daniel Reyes</div>
      <div class="title">Managing Director</div>
    </div>
    <div class="front-brand">
      <span class="brand-dot"></span>
      <span>Larkmoor<br>Trade Partners</span>
    </div>
    <div class="contact">
      <div class="address">Your address, City<br>State, Zip 1234</div>
      <div class="contact-line">123 456 789
        <svg viewBox="0 0 12 12"><circle cx="6" cy="6" r="6" fill="var(--white)"/><path d="M4 3.2l1 1.6-.7.7a4 4 0 0 0 2.2 2.2l.7-.7 1.6 1-.6 1.1C5.6 9 3 6.4 2.9 3.8z" fill="var(--navy)"/></svg>
      </div>
      <div class="contact-line">123 456 789
        <svg viewBox="0 0 12 12"><circle cx="6" cy="6" r="6" fill="var(--white)"/><path d="M4 3.2l1 1.6-.7.7a4 4 0 0 0 2.2 2.2l.7-.7 1.6 1-.6 1.1C5.6 9 3 6.4 2.9 3.8z" fill="var(--navy)"/></svg>
      </div>
      <div class="contact-line">info@yourmail.com
        <svg viewBox="0 0 12 12"><circle cx="6" cy="6" r="6" fill="var(--white)"/><rect x="3" y="4" width="6" height="4.2" fill="none" stroke="var(--navy)" stroke-width="0.9"/><path d="M3 4l3 2.4L9 4" fill="none" stroke="var(--navy)" stroke-width="0.9"/></svg>
      </div>
      <div class="contact-line">www.yourwebsite.com
        <svg viewBox="0 0 12 12"><circle cx="6" cy="6" r="6" fill="var(--white)"/><circle cx="6" cy="6" r="3.2" fill="none" stroke="var(--navy)" stroke-width="0.9"/><path d="M2.8 6h6.4M6 2.8c-1.6 2-1.6 4.4 0 6.4M6 2.8c1.6 2 1.6 4.4 0 6.4" fill="none" stroke="var(--navy)" stroke-width="0.8"/></svg>
      </div>
    </div>
  </section>

  <section class="card card-back" aria-label="Business card, brand side">
    <div class="back-brand">
      <span class="brand-dot"></span>
      <span>Larkmoor Trade Partners</span>
    </div>
    <div class="social-row" aria-label="Social media links">
      <span class="social-dot"></span>
      <span class="social-dot"></span>
      <span class="social-dot"></span>
      <span class="social-dot"></span>
      <span class="social-dot"></span>
      <span class="social-dot"></span>
    </div>
    <div class="back-edge"></div>
  </section>

</main>
</body>
</html>
```